Letter design, envelope design, and more

Hello, we the Tavrin Gmbh are looking for our shop. Letter C5. Design does not have to be like a business card, so it can have straight lines. Only the color is important. The logo is the text under TaVRin omit.It should not be playful but Profesionel

Font styles to use
Sans Serif

Colors
0555a3
3176b5
85abd2
85cae6
34a7d8
0792cd
cee9f5
cfdfed
000000

Requirements
Must have
• Color like business card, Please, with the text under TaVRin, Correct address Lindmattstr. 4 Zip code 9517 Goldach, as well as Couvert Without addressing only design and logo with TaVrn
Nice to have
• more writing articles
Should not have
• Not too colored, Text under TaVRin, bright colors

```html
<!DOCTYPE html>
<html lang="de">
<head>
<meta charset="utf-8">
<title>Tavrin Gmbh – Briefschaften</title>
<link rel="stylesheet" href="https://fonts.googleapis.com/css2?family=Roboto:wght@400;700&display=swap">
<style>
  :root {
    --backdrop: #d6d6d6;
    --paper: #f4f4f4;
    --brand-blue: #0555a3;
    --soft-blue: #85abd2;
    --ink: #000000;
    --white: #ffffff;
  }
  * { margin: 0; padding: 0; box-sizing: border-box; }
  html, body { width: 1200px; height: 810px; overflow: hidden; }
  body {
    position: relative;
    background: var(--backdrop);
    font-family: "Roboto", Arial, sans-serif;
    color: var(--ink);
  }
  .sheet {
    position: absolute;
    background: var(--paper);
    overflow: hidden;
    box-shadow: 0 8px 18px rgba(0,0,0,.18);
  }
  .letterhead { left: 137px; top: 110px; width: 436px; height: 614px; }
  .envelope-back { left: 619px; top: 193px; width: 444px; height: 222px; }
  .envelope-front { left: 618px; top: 444px; width: 445px; height: 221px; }

  .brand {
    position: absolute;
    display: flex;
    align-items: center;
    gap: 7px;
    color: var(--brand-blue);
    font-weight: 700;
    letter-spacing: .04em;
    white-space: nowrap;
  }
  .brand-square { background: var(--brand-blue); display: block; }
  .letterhead .brand { left: 37px; top: 54px; font-size: 19px; }
  .letterhead .brand-square { width: 30px; height: 30px; }
  .envelope-front .brand { left: 24px; top: 30px; font-size: 15px; }
  .envelope-front .brand-square { width: 24px; height: 24px; }

  .contact {
    position: absolute;
    font-style: normal;
    font-size: 7.5px;
    line-height: 10px;
    color: #4a4a4a;
  }
  .contact .gap { margin-top: 4px; }
  .contact .line { display: flex; align-items: center; gap: 4px; }
  .contact svg { width: 7px; height: 7px; fill: var(--brand-blue); flex: none; }
  .letterhead .contact { left: 334px; top: 52px; }
  .envelope-front .contact { left: 24px; top: 84px; }

  .swoosh { position: absolute; left: 0; bottom: 0; display: block; }
  .web {
    position: absolute;
    color: var(--white);
    font-size: 7.5px;
  }
  .letterhead .web { right: 37px; bottom: 7px; }
  .envelope-front .web { right: 45px; bottom: 8px; }

  .flap { position: absolute; left: 0; top: 0; display: block; }
  .flap-name {
    position: absolute;
    left: 0; right: 0; top: 23px;
    text-align: center;
    color: var(--white);
    font-weight: 700;
    font-size: 17px;
    letter-spacing: .08em;
  }
</style>
</head>
<body>

<section class="sheet letterhead" aria-label="Briefbogen">
  <div class="brand"><span class="brand-square"></span>TAVRIN GMBH</div>
  <address class="contact">
    <div>Lindmattstr. 4</div>
    <div>9517 Goldach</div>
    <div class="line gap"><svg viewBox="0 0 10 10"><path d="M2 0h2l1 3-1.5 1a6 6 0 0 0 2.5 2.5L7 5l3 1v2c0 1-1 2-2 2A8 8 0 0 1 0 2c0-1 1-2 2-2z"/></svg>+41 71 555 02 18</div>
    <div class="line"><svg viewBox="0 0 10 10"><path d="M0 2h10v6H0z M0 2l5 3.5L10 2" stroke="#f4f4f4" stroke-width=".8"/></svg>info@tavrin.ch</div>
  </address>
  <svg class="swoosh" width="436" height="40" viewBox="0 0 436 40">
    <path d="M43 40 Q190 10 362 8 Q230 14 100 40 Z" fill="var(--soft-blue)"/>
    <path d="M102 40 Q250 12 436 18 L436 40 Z" fill="var(--brand-blue)"/>
  </svg>
  <div class="web">www.tavrin.ch</div>
</section>

<section class="sheet envelope-back" aria-label="Couvert Rückseite">
  <svg class="flap" width="444" height="66" viewBox="0 0 444 66">
    <path d="M0 0H444L436 55Q434 65 424 65H20Q10 65 8 55Z" fill="var(--brand-blue)"/>
  </svg>
  <div class="flap-name">TAVRIN</div>
</section>

<section class="sheet envelope-front" aria-label="Couvert Vorderseite">
  <div class="brand"><span class="brand-square"></span>TAVRIN GMBH</div>
  <address class="contact">
    <div>Lindmattstr. 4</div>
    <div>9517 Goldach</div>
    <div class="line gap"><svg viewBox="0 0 10 10"><path d="M2 0h2l1 3-1.5 1a6 6 0 0 0 2.5 2.5L7 5l3 1v2c0 1-1 2-2 2A8 8 0 0 1 0 2c0-1 1-2 2-2z"/></svg>+41 71 555 02 18</div>
    <div class="line"><svg viewBox="0 0 10 10"><path d="M0 2h10v6H0z M0 2l5 3.5L10 2" stroke="#f4f4f4" stroke-width=".8"/></svg>info@tavrin.ch</div>
  </address>
  <svg class="swoosh" width="445" height="32" viewBox="0 0 445 32">
    <path d="M62 32 Q210 2 372 0 Q250 6 122 32 Z" fill="var(--soft-blue)"/>
    <path d="M124 32 Q270 4 445 9 L445 32 Z" fill="var(--brand-blue)"/>
  </svg>
  <div class="web">www.tavrin.ch</div>
</section>

</body>
</html>
```